Lumavento business card

We need a modern business card - With our 4 colors - See web: www.lumavento.dk

I have attached logo and som old business Cards we have - Lets Make the new ones shine...:-) -

Industry/Entity Type

Business

Requirements
Must have
• the logo with lumavento only,

```html
<!DOCTYPE html>
<html lang="da">
<head>
<meta charset="utf-8">
<title>Lumavento – visitkort</title>
<link rel="stylesheet" href="https://fonts.googleapis.com/css2?family=Didact+Gothic&family=Open+Sans:wght@400;600;700&display=swap">
<style>
  :root {
    --magenta: #e6008a;
    --lime: #a5c83a;
    --plum: #74256f;
    --orange: #f27b22;
    --soft-pink: #f8cde5;
    --soft-lime: #eef4da;
    --soft-plum: #e4d6e6;
    --soft-peach: #fde6d6;
    --ink-plum: #6a2468;
    --ink-dark: #3b2f3a;
    --ink-grey: #5b5b5b;
    --white: #ffffff;
    --stage: #efece8;
  }
  * { box-sizing: border-box; margin: 0; padding: 0; }
  html, body { width: 1200px; height: 900px; overflow: hidden; }
  body { background: var(--stage); position: relative; font-family: "Open Sans", sans-serif; }

  .card {
    position: absolute;
    width: 560px;
    height: 362px;
    overflow: hidden;
    box-shadow: 0 6px 18px rgba(0,0,0,0.12);
    display: flex;
    flex-direction: column;
  }
  .card .band { width: 100%; flex: none; }

  /* Back side */
  .card--back { left: 110px; top: 70px; }
  .card--back .band--magenta { height: 17%; background: var(--magenta); }
  .card--back .band--lime { height: 24%; background: var(--lime); }
  .card--back .band--plum { height: 27%; background: var(--plum); }
  .card--back .band--orange { height: 32%; background: var(--orange); }

  .back-identity {
    position: absolute;
    left: 0; right: 0;
    top: 41%;
    height: 27%;
    display: flex;
    flex-direction: column;
    align-items: center;
    justify-content: center;
    font-family: "Didact Gothic", sans-serif;
    color: var(--white);
    letter-spacing: 0.08em;
  }
  .back-identity__name { font-size: 20px; line-height: 1.2; }
  .back-identity__rule { width: 62%; height: 3px; background: var(--white); margin: 6px 0 5px; border-radius: 2px; }
  .back-identity__title { font-size: 18px; line-height: 1.2; }

  /* Front side */
  .card--front { left: 530px; top: 468px; }
  .card--front .band--pink { height: 30%; background: var(--soft-pink); }
  .card--front .band--lime { height: 23%; background: var(--soft-lime); }
  .card--front .band--plum { height: 26%; background: var(--soft-plum); }
  .card--front .band--peach { height: 21%; background: var(--soft-peach); }

  .brand {
    position: absolute;
    left: 34px;
    top: 118px;
    width: 240px;
    text-align: center;
  }
  .brand__name {
    display: flex;
    align-items: center;
    justify-content: center;
    gap: 10px;
    font-family: "Didact Gothic", sans-serif;
    font-size: 24px;
    line-height: 1.2;
    letter-spacing: 0.14em;
    color: var(--ink-grey);
  }
  .brand__dot { width: 14px; height: 14px; border-radius: 50%; background: var(--lime); }
  .brand__rule { height: 3px; background: var(--lime); margin: 12px 0 8px; }
  .brand__tagline { font-family: "Didact Gothic", sans-serif; font-size: 15px; color: var(--ink-grey); }

  .contact {
    position: absolute;
    left: 318px;
    top: 96px;
    color: var(--ink-dark);
    font-size: 12.5px;
    line-height: 1.35;
    white-space: nowrap;
  }
  .contact__name { font-size: 18px; font-weight: 700; color: var(--ink-plum); line-height: 1.25; }
  .contact__title { font-size: 12.5px; margin-bottom: 20px; padding-left: 10px; }
  .contact__address { margin-bottom: 14px; padding-left: 24px; }
  .contact__list { list-style: none; padding-left: 24px; }
  .contact__list li { display: flex; align-items: center; gap: 8px; margin-bottom: 3px; }
  .contact__icon { width: 14px; height: 14px; flex: none; }
</style>
</head>
<body>

<section class="card card--back" aria-label="Visitkort, bagside">
  <div class="band band--magenta"></div>
  <div class="band band--lime"></div>
  <div class="band band--plum"></div>
  <div class="band band--orange"></div>
  <div class="back-identity">
    <p class="back-identity__name">Maren Holmgaard</p>
    <div class="back-identity__rule"></div>
    <p class="back-identity__title">Salgsdirektør</p>
  </div>
</section>

<section class="card card--front" aria-label="Visitkort, forside">
  <div class="band band--pink"></div>
  <div class="band band--lime"></div>
  <div class="band band--plum"></div>
  <div class="band band--peach"></div>

  <div class="brand">
    <p class="brand__name"><span class="brand__dot"></span>lumavento</p>
    <div class="brand__rule"></div>
    <p class="brand__tagline">Medier til unge</p>
  </div>

  <div class="contact">
    <p class="contact__name">Maren Holmgaard</p>
    <p class="contact__title">Salgsdirektør</p>
    <p class="contact__address">Kastanjevej 8 - 5200<br>Odense V - Tlf. 38 40 12 70</p>
    <ul class="contact__list">
      <li>
        <svg class="contact__icon" viewBox="0 0 16 16" aria-hidden="true"><path fill="#6a2468" d="M4 1.5l2.2 2.6-1.3 1.6c.9 2 2.4 3.5 4.4 4.4l1.6-1.3 2.6 2.2-1.4 2.2C6.8 12.9 3.1 9.2 1.8 3z"/></svg>
        <span>+45 60 21 34 87</span>
      </li>
      <li>
        <svg class="contact__icon" viewBox="0 0 16 16" aria-hidden="true"><rect x="1.5" y="3.5" width="13" height="9" rx="1" fill="#6a2468"/><path d="M2 4.2l6 4.6 6-4.6" fill="none" stroke="#e4d6e6" stroke-width="1.2"/></svg>
        <span>mh@lumavento.dk</span>
      </li>
      <li>
        <svg class="contact__icon" viewBox="0 0 16 16" aria-hidden="true"><circle cx="8" cy="8" r="6.5" fill="#6a2468"/><path d="M1.5 8h13M8 1.5c-3 3.5-3 9.5 0 13M8 1.5c3 3.5 3 9.5 0 13" fill="none" stroke="#fde6d6" stroke-width="0.9"/></svg>
        <span>www.lumavento.dk</span>
      </li>
    </ul>
  </div>
</section>

</body>
</html>
```